Creative, fresh business card design for Ripplecraft Facades

We need a fresh, creative business card design for Ripplecraft Facades. We are the manufacturer of Ripplecraft Facades in Australia. Wall panels are 2400 x 1200mm panels made from MDF and feature 3D patterns on the face of the panel. The colours to be used are green, silver/grey and white RGB
Red 187
Green 207
Blue 65.

An idea is to possibly use a watermark of one of our designs as a background (like on the "Grids" design on the left hand side of page 2 of our brochure).

Target Market(s)

Interior designers, architects, builders and home renovators

Industry/Entity Type

Business

Contact Information for Business Card

Details to go on the card are:
Our logo (attached),
Slogan: "Decorative panels for interiors and exteriors",
Contact name,
Position,
Mobile phone number,
Business address,
Business phone,
Business fax,
Website and
Email address.

I have attached a few images of our panels and our brochure for reference.

The colours of the business card should feature our logo colours which are: RGB
Red 187
Green 207
Blue 65

Requirements
Must have
• Very modern fonts and design. Some of the designs shown especially the "Prisms" design which is a popular design.
Nice to have
• Creative but simple design. Very contemporary.
Should not have
• Anything ornate or old fashioned.

```html
<!DOCTYPE html>
<html lang="en">
<head>
<meta charset="utf-8">
<title>Ripplecraft Facades – Business Card</title>
<link href="https://fonts.googleapis.com/css2?family=Arimo:wght@400;700&display=swap" rel="stylesheet">
<style>
  :root {
    --brand-green: rgb(187, 207, 65);
    --brand-grey: #8e8f93;
    --ink: #4a4a4c;
    --paper: #ffffff;
    --backdrop: #e8e6e2;
  }
  * { margin: 0; padding: 0; box-sizing: border-box; }
  html, body {
    width: 1200px;
    height: 987px;
    overflow: hidden;
    background: var(--backdrop);
    font-family: "Arimo", Arial, sans-serif;
  }
  .canvas {
    position: relative;
    width: 1200px;
    height: 987px;
  }
  .card {
    position: absolute;
    width: 615px;
    height: 350px;
    box-shadow: 0 3px 10px rgba(0, 0, 0, 0.18);
  }
  .card--front { left: 293px; top: 131px; background: var(--paper); }
  .card--back  { left: 292px; top: 506px; background: var(--brand-grey); }

  /* brand lockup */
  .brand {
    display: flex;
    align-items: center;
    gap: 12px;
  }
  .brand__square {
    width: 44px;
    height: 44px;
    background: var(--brand-green);
    flex: none;
  }
  .brand__name {
    font-size: 25px;
    font-weight: 400;
    letter-spacing: -0.3px;
  }
  .tagline {
    font-size: 12px;
    letter-spacing: 2.2px;
    line-height: 16px;
  }

  .card--front .brand { position: absolute; left: 32px; top: 34px; }
  .card--front .brand__name { color: var(--brand-grey); }
  .card--front .tagline { position: absolute; left: 33px; top: 146px; color: var(--brand-grey); }

  .contact {
    position: absolute;
    right: 29px;
    top: 218px;
    text-align: right;
    color: var(--ink);
    font-size: 15.5px;
  }
  .contact__name {
    font-size: 21px;
    font-weight: 700;
    color: var(--brand-green);
    margin-bottom: 9px;
  }
  .contact__role {
    font-weight: 400;
    font-size: 17px;
    color: var(--brand-grey);
  }
  .contact__line { margin-bottom: 7px; }
  .contact__label { color: var(--brand-green); font-weight: 700; margin-left: 8px; }
  .contact__label:first-child { margin-left: 0; }

  .edge-tab {
    position: absolute;
    right: 0;
    top: 228px;
    width: 14px;
    height: 91px;
    background: var(--brand-grey);
  }

  .card--back .lockup {
    position: absolute;
    left: 0;
    right: 0;
    top: 108px;
    display: flex;
    flex-direction: column;
    align-items: center;
  }
  .card--back .brand__square { width: 52px; height: 52px; }
  .card--back .brand__name { color: var(--paper); font-size: 28px; }
  .card--back .tagline {
    color: var(--paper);
    margin-top: 22px;
    text-align: center;
    font-size: 13px;
    letter-spacing: 2.6px;
  }
</style>
</head>
<body>
  <main class="canvas">
    <section class="card card--front" aria-label="Business card front">
      <div class="brand">
        <span class="brand__square"></span>
        <span class="brand__name">Ripplecraft Facades</span>
      </div>
      <p class="tagline">decorative panels for<br>interiors &amp; landscapes</p>

      <div class="contact">
        <p class="contact__name">MAREN HOLT - <span class="contact__role">CEO&amp;Founder</span></p>
        <p class="contact__line">412 Tidewater Road, Geelong, Victoria 3220</p>
        <p class="contact__line"><span class="contact__label">P :</span> (03) 5521 4087 <span class="contact__label">F :</span> (03) 5521 4099</p>
        <p class="contact__line"><span class="contact__label">E :</span> mholt@ripplecraftfacades.com <span class="contact__label">W :</span> www.ripplecraftfacades.com</p>
      </div>
      <span class="edge-tab"></span>
    </section>

    <section class="card card--back" aria-label="Business card back">
      <div class="lockup">
        <div class="brand">
          <span class="brand__square"></span>
          <span class="brand__name">Ripplecraft Facades</span>
        </div>
        <p class="tagline">decorative panels for<br>interiors &amp; landscapes</p>
      </div>
    </section>
  </main>
</body>
</html>
```